Quorva - corporate Business Card

We need a good look and innovative business card for a new start up company based in Los Angeles called "Quorva". We are in a payment business, including payment card, app, and ewallet. We are expert in online payment and Card not present (CNP) transaction.
We need an innovative, modern business card.

Our logo font is Aero Matics

Target Market(s)

Startup - Bank - Online Payment - Card Manufacturing

Industry/Entity Type

Startup

Contact Information for Business Card

phone: 555 014 7396 - Address: 4172 Marlowe blvd, Brenwick City, OR 97299

Requirements
Must have
• Message: innovative, professional, expert, high tech, trust, online payment expert, security
Nice to have
• no comment
Should not have
• no Comment

```html
<!DOCTYPE html>
<html lang="en">
<head>
<meta charset="utf-8">
<title>Quorva – Business Card</title>
<link rel="stylesheet" href="https://fonts.googleapis.com/css2?family=Exo+2:wght@600&family=Open+Sans:wght@400;700&display=swap">
<style>
  :root {
    --backdrop: #bdbdbd;
    --brand-red: #c8102e;
    --red-deep: #a8000f;
    --red-light: #d6263a;
    --paper: #ffffff;
    --ink-grey: #7a7a7a;
    --card-shadow: rgba(0, 0, 0, 0.22);
  }
  * { margin: 0; padding: 0; box-sizing: border-box; }
  html, body {
    width: 1200px;
    height: 837px;
    overflow: hidden;
    background: var(--backdrop);
  }
  .canvas {
    position: relative;
    width: 1200px;
    height: 837px;
    display: flex;
    align-items: center;
    justify-content: center;
    gap: 60px;
  }
  .card {
    position: relative;
    width: 500px;
    height: 286px;
    border-radius: 3px;
    overflow: hidden;
    box-shadow: 0 10px 24px var(--card-shadow);
  }
  /* Front side */
  .card--front {
    background: linear-gradient(120deg, var(--red-deep) 0%, var(--brand-red) 55%, var(--red-light) 100%);
    display: flex;
    align-items: center;
    justify-content: center;
  }
  .front__halo {
    position: absolute;
    left: -40px;
    top: -10px;
    width: 300px;
    height: 300px;
    border-radius: 50%;
    background: rgba(0, 0, 0, 0.06);
  }
  .wordmark {
    font-family: "Exo 2", sans-serif;
    font-weight: 600;
    letter-spacing: 1px;
    line-height: 1;
  }
  .card--front .wordmark {
    position: relative;
    color: var(--paper);
    font-size: 64px;
  }
  /* Back side */
  .card--back {
    background: var(--paper);
    display: flex;
    flex-direction: column;
    align-items: center;
    padding-top: 52px;
  }
  .logo-lockup {
    display: flex;
    align-items: center;
    gap: 12px;
  }
  .logo-lockup__dot {
    width: 52px;
    height: 52px;
    border-radius: 50%;
    background: var(--brand-red);
  }
  .card--back .wordmark {
    color: var(--brand-red);
    font-size: 54px;
  }
  .person {
    margin-top: 26px;
    text-align: center;
    font-family: "Open Sans", sans-serif;
  }
  .person__name {
    color: var(--brand-red);
    font-weight: 700;
    font-size: 15px;
    line-height: 1.1;
  }
  .person__role {
    color: var(--ink-grey);
    font-size: 12px;
  }
  .contact {
    margin-top: 14px;
    font-family: "Open Sans", sans-serif;
    color: var(--ink-grey);
    font-size: 12px;
    text-align: center;
    line-height: 1.6;
  }
  .contact__phone {
    display: inline-flex;
    align-items: center;
    gap: 5px;
  }
  .contact__icon {
    width: 13px;
    height: 13px;
  }
</style>
</head>
<body>
  <main class="canvas">
    <section class="card card--front" aria-label="Card front">
      <div class="front__halo"></div>
      <span class="wordmark">quorva</span>
    </section>

    <section class="card card--back" aria-label="Card back">
      <div class="logo-lockup">
        <span class="logo-lockup__dot"></span>
        <span class="wordmark">quorva</span>
      </div>
      <div class="person">
        <p class="person__name">Jordan Hale</p>
        <p class="person__role">Managing Director</p>
      </div>
      <div class="contact">
        <p class="contact__address">4172 Marlowe blvd, Brenwick City, OR 97299</p>
        <p class="contact__phone">
          <svg class="contact__icon" viewBox="0 0 16 16" aria-hidden="true">
            <circle cx="8" cy="8" r="8" fill="var(--brand-red)"/>
            <path d="M5.2 4.2l1.4 1.6-.7.9c.5 1 1.3 1.8 2.3 2.3l.9-.7 1.6 1.4-.8 1.3c-2.8-.4-4.6-2.2-5-5z" fill="#fff"/>
          </svg>
          555 014 7396
        </p>
      </div>
    </section>
  </main>
</body>
</html>
```